Counseling Practice Business Card

I need a professional looking business card incorporating my new logo that was just completed. Card needs to incorporate my name and title, description of my specialty, my address, my phone number, my fax number, my email and my website URL. I need to be able to choose design on/with different paper colors and textures.
I do not have a lot of business card ideas so I am open to anything but I want bold,sharp, clear card without additional designs other than my logo (see attached file info). I am open to different color backgrounds or paper colors including black. I do not like traditional brackets around area codes in phone number or dashes between numbers in phone number. Am open to other ways of presenting including periods between numbers as appropriate. I do not know enough to know what I like yet but I want card to coordinate and work together with my logo. My practice emphasizes natural mental health interventions so any use of color (with background paper color or the blue and green in my logo) that elicits nature is nice. In addition to black, any natural brown or wood looking background might be desirable also. Most of the offerings so far look very similar and boring.

Target Market(s)

Potential therapy clients and other professionals

Contact Information for Business Card

Card information:
Gerald M. Whitcombe, Ph.D.
Licensed Clinical Psychologist
Integrative Health Coach
4812 Marlowe Ridge Blvd SE
Suite 310
Duluth, GA 30096
(770) 415-2983 phone
(770) 581-4096 fax
drgeraldwhitcombe@quillmarsh.net
brightfernwellness.net

Font styles to use
Serif
Sans Serif
Other font styles liked:
• anything that you think looks crisp, clear and easily readable

Requirements
Must have
• Any color used should coordinate with my logo design (see attached files).
• Card should be printed horizontally so top and bottom are longest sides of rectangle.
• Background color or paper color should complement and highlight logo. Do not like a white background. black, grey, brown or any color my logo would blend well with.
Nice to have
• I would like designer to utilize color to highlight letters/name or phone-fax-web symbols.
• Bottom edge of card could be highlighted if appropriate to an idea.
Should not have
• I would NOT want the card to have a pure white background at all.
• No clear cards.
• Cards should be oriented with long sides on bottom and top, NOT sides. DO NOT LIKE THIS THIN TALL ORIENTATION.

```html
<!DOCTYPE html>
<html lang="en">
<head>
<meta charset="utf-8">
<title>Brightfern Wellness Business Card</title>
<link href="https://fonts.googleapis.com/css2?family=Lato:wght@400;700;900&display=swap" rel="stylesheet">
<style>
  :root {
    --backdrop: #3a3b3d;
    --brand-blue: #2a74b6;
    --brand-green: #137238;
    --ink: #2b2b2b;
    --ink-soft: #3c3c3c;
    --paper: #f3f0e7;
    --on-blue: #ffffff;
  }
  * { box-sizing: border-box; margin: 0; padding: 0; }
  html, body { width: 1200px; height: 1200px; overflow: hidden; }
  body {
    background: var(--backdrop);
    font-family: "Lato", Arial, sans-serif;
    position: relative;
  }
  .card {
    position: absolute;
    left: 180px;
    width: 840px;
    height: 480px;
    border-radius: 36px;
    overflow: hidden;
  }
  /* Back side */
  .card-back { top: 70px; background: var(--brand-blue); color: var(--on-blue); }
  .card-back .brand-name {
    position: absolute; left: 0; right: 0; top: 170px;
    text-align: center; font-weight: 700; font-size: 54px; letter-spacing: 1px;
  }
  .card-back .web-address {
    position: absolute; left: 0; right: 0; top: 360px;
    text-align: center; font-size: 24px; letter-spacing: 0.5px;
  }
  .rule { position: absolute; height: 1px; background: rgba(255,255,255,0.75); }
  .rule-upper { top: 262px; left: 600px; right: 0; }
  .rule-lower { top: 420px; left: 0; width: 260px; }

  /* Front side */
  .card-front { top: 640px; background: var(--paper); color: var(--ink); }
  .card-front .brand-name {
    position: absolute; left: 30px; width: 400px; top: 180px;
    text-align: center; font-weight: 700; font-size: 40px; color: var(--brand-blue);
  }
  .divider {
    position: absolute; left: 445px; top: 120px; width: 1.5px; height: 210px;
    background: var(--brand-blue);
  }
  .contact-block { position: absolute; left: 466px; top: 70px; right: 14px; }
  .person-name {
    font-weight: 900; font-size: 19px; color: var(--brand-blue);
    text-transform: uppercase; letter-spacing: 0.2px; white-space: nowrap;
  }
  .person-title { font-size: 17px; line-height: 1.3; color: var(--ink-soft); margin-top: 8px; }
  .contact-list { list-style: none; margin-top: 26px; }
  .contact-list li {
    display: flex; align-items: center; gap: 12px;
    font-size: 18px; color: var(--ink-soft); margin-bottom: 9px; white-space: nowrap;
  }
  .contact-list svg { width: 22px; height: 18px; flex: none; }
  .address-band {
    position: absolute; left: 0; bottom: 0; width: 480px; height: 112px;
    background: var(--brand-blue); border-top-right-radius: 16px;
    color: var(--on-blue); display: flex; align-items: center; gap: 14px; padding-left: 40px;
  }
  .address-band svg { width: 22px; height: 30px; flex: none; }
  .address-text { font-size: 21px; line-height: 1.3; }
  .green-strip {
    position: absolute; right: 0; bottom: 0; left: 380px; height: 40px;
    background: var(--brand-green); border-top-left-radius: 20px;
  }
  .card-front .web-address {
    position: absolute; right: 40px; bottom: 58px;
    font-size: 20px; color: var(--ink); letter-spacing: 0.3px;
  }
</style>
</head>
<body>

<section class="card card-back" aria-label="Business card back">
  <div class="brand-name">Brightfern Wellness</div>
  <div class="rule rule-upper"></div>
  <div class="web-address">www.brightfernwellness.net</div>
  <div class="rule rule-lower"></div>
</section>

<section class="card card-front" aria-label="Business card front">
  <div class="brand-name">Brightfern Wellness</div>
  <div class="divider"></div>

  <div class="contact-block">
    <h1 class="person-name">Gerald M. Whitcombe, Ph.D.</h1>
    <p class="person-title">Licensed Clinical Psychologist/<br>Integrative Health Coach</p>
    <ul class="contact-list">
      <li>
        <svg viewBox="0 0 22 18" aria-hidden="true"><path fill="#2a74b6" d="M2 6c0-3 4-4 9-4s9 1 9 4v2h-5V6H7v2H2z M5 9h12l2 7H3z"/><circle cx="11" cy="12" r="2" fill="#f3f0e7"/></svg>
        <span>770.415.2983</span>
      </li>
      <li>
        <svg viewBox="0 0 22 18" aria-hidden="true"><g fill="none" stroke="#2a74b6" stroke-width="1.5"><rect x="6" y="1" width="10" height="6"/><rect x="2" y="7" width="18" height="9" rx="1"/><line x1="5" y1="11" x2="12" y2="11"/></g></svg>
        <span>770.581.4096</span>
      </li>
      <li>
        <svg viewBox="0 0 22 18" aria-hidden="true"><g fill="none" stroke="#2a74b6" stroke-width="1.5"><rect x="1" y="2" width="20" height="14"/><polyline points="1,2 11,10 21,2"/></g></svg>
        <span>drgeraldwhitcombe@quillmarsh.net</span>
      </li>
    </ul>
  </div>

  <div class="green-strip"></div>
  <div class="address-band">
    <svg viewBox="0 0 22 30" aria-hidden="true"><path fill="#fff" d="M11 1a10 10 0 0 0-10 10c0 7 10 18 10 18s10-11 10-18A10 10 0 0 0 11 1z"/><circle cx="11" cy="11" r="4" fill="#2a74b6"/></svg>
    <p class="address-text">4812 Marlowe Ridge Blvd SE, Suite 310<br>Duluth, GA 30096</p>
  </div>
  <div class="web-address">www.brightfernwellness.net</div>
</section>

</body>
</html>
```